New Fun, Positive, energised looking Business Card Needed for High Achiever Coach

I am looking for a two sided full colour business card. I am self employed and have recently re branded my 1-2-1 work Renewing Driven Leaders. My target client base for these cards is therefore high achievers - usually aged 40 -55, they are often entrepreneurs, CEO or work in banking and finance and 2/3 are male. I work with them on 90 day or 6 month coaching programs to help them live their success in a healthier, more sustainable and fulfiiled way. They pay for this privately so though they are corporate types the cards need not look 'corporate'. I want to portray the idea of transformation, vitality and re-connecting.
You can get a feel for the look I like on my new website: morvenlisk.co.uk
I want to use this logo with strapline (Renewing Driven Leaders) (I purchased off Logoharbor) and font/ colours (the turquoise and green).
Details to include on the card:
www.morvenlisk.co.uk
+44 7915 302618
morven@morvenlisk.co.uk
skype: morvenlisk
I'd also like to include:
Do you struggle to switch off? Want to be healthier and feel fitter? Want closer relationships? More clarity over the direction you are headed? I can help you do these things using integrated mind-body techniques. Visit morvenlisk.co.uk TODAY to apply for a FREE Breakthrough session.
BUT if that is too much text for a card I am open to advice/ammendments.
Updates
Thanks for your design - I am considering them. PLease change the wording to :

```html
<!DOCTYPE html>
<html lang="en">
<head>
<meta charset="utf-8">
<title>Morven Lisk – Business Card</title>
<link rel="stylesheet" href="https://fonts.googleapis.com/css2?family=Arvo:wght@700&family=Great+Vibes&family=Open+Sans:wght@400&display=swap">
<style>
  :root {
    --turquoise: #0ba0c3;
    --turquoise-deep: #0890b2;
    --green: #5db865;
    --paper: #f7f8f8;
    --ink: #3c4a55;
    --backdrop: #e9eaec;
    --white: #ffffff;
  }
  * { box-sizing: border-box; margin: 0; padding: 0; }
  html, body { width: 1200px; height: 900px; overflow: hidden; }
  body {
    background: var(--backdrop);
    display: flex;
    flex-direction: column;
    align-items: center;
    justify-content: center;
    gap: 40px;
    font-family: "Open Sans", Arial, sans-serif;
  }
  .card {
    position: relative;
    width: 665px;
    height: 380px;
    overflow: hidden;
    box-shadow: 0 6px 18px rgba(0,0,0,0.12);
  }

  /* Front */
  .card-front { background: var(--paper); }
  .edge-left-top, .edge-left-bottom {
    position: absolute; left: 0; width: 12px;
  }
  .edge-left-top { top: 0; height: 55%; background: var(--green); }
  .edge-left-bottom { bottom: 0; height: 45%; background: var(--turquoise); }
  .edge-bottom {
    position: absolute; left: 0; right: 0; bottom: 0; height: 10px;
    background: var(--green);
  }
  .holder-name {
    position: absolute; right: 70px; top: 62px;
    font-family: "Great Vibes", cursive;
    font-size: 46px;
    line-height: 1.2;
    color: var(--green);
  }
  .name-rule {
    position: absolute; right: 30px; top: 150px; width: 330px; height: 2px;
    background: var(--turquoise);
  }
  .brand-front {
    position: absolute; left: 40px; bottom: 36px;
  }
  .brand-name {
    font-family: "Arvo", Georgia, serif;
    font-weight: 700;
    font-size: 21px;
    line-height: 1.2;
    color: var(--turquoise);
    display: flex; align-items: center; gap: 8px;
    white-space: nowrap;
  }
  .brand-dot {
    width: 12px; height: 12px; border-radius: 50%;
    background: var(--green);
  }
  .strapline {
    font-family: "Great Vibes", cursive;
    font-size: 17px;
    line-height: 1.3;
    color: var(--turquoise);
    white-space: nowrap;
  }
  .brand-front .strapline { padding-left: 20px; }
  .contacts {
    position: absolute; right: 36px; bottom: 44px;
    display: flex; align-items: center; gap: 20px;
    font-size: 12.5px; color: var(--ink);
  }
  .contact-column { display: flex; flex-direction: column; gap: 8px; }
  .contact-item { display: flex; align-items: center; gap: 8px; white-space: nowrap; }
  .contact-icon { width: 15px; height: 15px; flex: none; }
  .contact-divider { width: 2px; height: 40px; background: var(--turquoise); }

  /* Back */
  .card-back {
    background: radial-gradient(ellipse at 45% 40%, #12aed0 0%, var(--turquoise) 55%, var(--turquoise-deep) 100%);
    display: flex; align-items: center; justify-content: center;
  }
  .brand-back { text-align: center; color: var(--white); }
  .brand-back .brand-mark {
    width: 64px; height: 64px; border-radius: 50%;
    border: 5px solid var(--white);
    margin: 0 auto 20px;
  }
  .brand-back .brand-name {
    color: var(--white); font-size: 48px; justify-content: center;
  }
  .brand-back .strapline { color: var(--white); font-size: 28px; margin-top: 4px; }
</style>
</head>
<body>

  <section class="card card-front" aria-label="Business card front">
    <span class="edge-left-top"></span>
    <span class="edge-left-bottom"></span>
    <span class="edge-bottom"></span>

    <p class="holder-name">Your Name</p>
    <span class="name-rule"></span>

    <div class="brand-front">
      <p class="brand-name"><span class="brand-dot"></span>Morven Lisk</p>
      <p class="strapline">Renewing Driven Leaders</p>
    </div>

    <div class="contacts">
      <div class="contact-column">
        <p class="contact-item">
          <svg class="contact-icon" viewBox="0 0 16 16"><circle cx="8" cy="8" r="8" fill="var(--ink)"/><path d="M5 4.5c.6-.4 1.2 0 1.5.6l.5 1c.2.4 0 .8-.3 1l-.4.3c.4 1 1.2 1.8 2.2 2.2l.3-.4c.2-.3.6-.5 1-.3l1 .5c.6.3 1 .9.6 1.5-.6.8-1.5 1-2.4.6C7 10.7 5.3 9 4.6 7c-.4-.9-.2-1.8.4-2.5z" fill="var(--white)"/></svg>
          +44 7915 302618
        </p>
        <p class="contact-item">
          <svg class="contact-icon" viewBox="0 0 16 16"><rect x="1" y="3.5" width="14" height="9" rx="1.5" fill="var(--ink)"/><path d="M2 4.5l6 4.5 6-4.5" fill="none" stroke="var(--white)" stroke-width="1.2"/></svg>
          morven@morvenlisk.co.uk
        </p>
      </div>
      <span class="contact-divider"></span>
      <div class="contact-column">
        <p class="contact-item">
          <svg class="contact-icon" viewBox="0 0 16 16"><circle cx="8" cy="8" r="8" fill="var(--ink)"/></svg>
          morvenlisk
        </p>
        <p class="contact-item">
          <svg class="contact-icon" viewBox="0 0 16 16"><circle cx="8" cy="8" r="8" fill="var(--ink)"/><g fill="none" stroke="var(--white)" stroke-width="1"><circle cx="8" cy="8" r="5.5"/><ellipse cx="8" cy="8" rx="2.4" ry="5.5"/><path d="M2.5 8h11"/></g></svg>
          www.morvenlisk.co.uk
        </p>
      </div>
    </div>
  </section>

  <section class="card card-back" aria-label="Business card back">
    <div class="brand-back">
      <div class="brand-mark"></div>
      <p class="brand-name">Morven Lisk</p>
      <p class="strapline">Renewing Driven Leaders</p>
    </div>
  </section>

</body>
</html>
```